Dorwin's Coating & Renewal Letterhead Design We want to revamp out old traditional letterhead with the new logo designs that are attached. We are working on getting all our company items from vehicles, business, cards, t-shirts, letterhead to match. This should include company colors, fonts, and flow of items that we have attached below.

Industry/Entity Type

Construction Company

Font styles to use
Sans Serif
Other font styles liked:
• Bold with outline

Colors
ec1f27
ffffff

Requirements
Must have
• Company Name: Dorwin's Coating & Renewal
• Address: 4728 SW 81st Ter Halverd cove fl 39417
• Office Number: (555) 413-2986
• Email: Dorwinrenewal@mailbrook.example
• License Number: KRT8046392
Nice to have
• Company Colors: red, white, black, and grey

```html
<!DOCTYPE html>
<html lang="en">
<head>
<meta charset="utf-8">
<title>Dorwin's Coating &amp; Renewal — Letterhead</title>
<link rel="stylesheet" href="https://fonts.googleapis.com/css2?family=Montserrat:wght@400;500;600;700;800&display=swap">
<style>
  :root {
    --brand-red: #ec1f27;
    --brand-orange: #ef4b27;
    --ink: #333333;
    --paper: #ffffff;
    --swoosh-grey: #e8e8e8;
    --swoosh-blush: #fadad1;
  }
  * { margin: 0; padding: 0; box-sizing: border-box; }
  html, body { width: 887px; height: 1200px; overflow: hidden; background: var(--paper); }
  body { font-family: "Montserrat", sans-serif; color: var(--ink); }

  .letterhead { position: relative; width: 887px; height: 1200px; background: var(--paper); overflow: hidden; }

  .swooshes { position: absolute; inset: 0; width: 887px; height: 1200px; }

  .brand-name {
    position: absolute; left: 63px; top: 52px;
    font-weight: 800; font-size: 30px; line-height: 1.05;
    color: var(--brand-orange); letter-spacing: 0.5px;
  }

  .contact { position: absolute; right: 95px; top: 52px; list-style: none; text-align: right; }
  .contact li {
    position: relative; font-weight: 700; font-size: 15.5px; line-height: 20.5px;
    padding-right: 26px; color: var(--ink);
  }
  .contact .icon { position: absolute; right: 0; top: 1px; width: 18px; height: 18px; }

  .header-rule { position: absolute; left: 370px; right: 0; top: 136px; height: 2px; background: var(--brand-red); }

  .sign-off { position: absolute; left: 63px; top: 240px; }
  .sign-off .closing { font-size: 13.5px; }
  .sign-off .name { margin-top: 14px; font-size: 24px; font-weight: 700; letter-spacing: 0.5px; line-height: 1; }
  .sign-off .role { font-size: 16px; font-weight: 700; line-height: 1.3; }

  .body-copy { position: absolute; left: 63px; font-size: 14.2px; line-height: 28px; white-space: nowrap; }
  .body-copy.p1 { top: 458px; }
  .body-copy.p2 { top: 654px; }
  .body-copy.p3 { top: 793px; }

  .footer-rule { position: absolute; left: 0; right: 0; top: 1142px; height: 2px; background: var(--brand-red); }
  .footer { position: absolute; left: 63px; right: 95px; top: 1160px; display: flex; justify-content: space-between; font-weight: 700; font-size: 17.5px; }
  .footer .license { color: var(--brand-red); }
</style>
</head>
<body>
<main class="letterhead">
  <svg class="swooshes" viewBox="0 0 1350 1909" preserveAspectRatio="none" aria-hidden="true">
    <path d="M0,427 Q700,360 1162,0 L1290,0 Q800,420 0,445 Z" fill="var(--swoosh-grey)"/>
    <path d="M804,337 Q1150,230 1350,47 L1350,127 Q1150,260 804,337 Z" fill="var(--swoosh-grey)"/>
    <path d="M309,1909 Q500,1820 789,1757 Q600,1830 420,1909 Z" fill="var(--swoosh-blush)"/>
    <path d="M789,1909 Q1000,1820 1350,1752 Q1150,1830 910,1909 Z" fill="var(--swoosh-blush)"/>
  </svg>

  <div class="brand-name">Dorwin's<br>Coating &amp; Renewal</div>

  <ul class="contact">
    <li>(555) 413-2986
      <svg class="icon" viewBox="0 0 18 18"><circle cx="9" cy="9" r="8" fill="none" stroke="var(--brand-orange)" stroke-width="1.3"/><path d="M6.3,5 L7.6,4.8 L8.3,6.8 L7.4,7.6 Q8.2,9.6 10.3,10.6 L11.1,9.7 L13,10.4 L12.9,11.7 Q9.8,12.6 7.3,10 Q5.2,7.7 6.3,5 Z" fill="var(--brand-orange)"/></svg>
    </li>
    <li>Dorwinrenewal@mailbrook.example
      <svg class="icon" viewBox="0 0 18 18"><circle cx="9" cy="9" r="8" fill="none" stroke="var(--brand-orange)" stroke-width="1.3"/><rect x="5.2" y="6.3" width="7.6" height="5.4" fill="var(--brand-orange)"/><path d="M5.2,6.3 L9,9.3 L12.8,6.3" fill="none" stroke="#fff" stroke-width="0.8"/></svg>
    </li>
    <li>www.dorwinrenewal.example
      <svg class="icon" viewBox="0 0 18 18"><circle cx="9" cy="9" r="8" fill="none" stroke="var(--brand-orange)" stroke-width="1.3"/><g fill="none" stroke="var(--brand-orange)" stroke-width="0.8"><circle cx="9" cy="9" r="4.5"/><ellipse cx="9" cy="9" rx="2" ry="4.5"/><line x1="4.5" y1="9" x2="13.5" y2="9"/></g></svg>
    </li>
  </ul>

  <div class="header-rule"></div>

  <section class="sign-off">
    <p class="closing">Sincearly,</p>
    <p class="name">MARLO KEENE</p>
    <p class="role">Director</p>
  </section>

  <p class="body-copy p1">This is a sample letter that has been placed to demonstrate typing remat (Your Company).letterhead<br>design. When positioned properly, it will serve to work in harmony with all other elements letterhead.<br>This letterhead design is meant to project an image&nbsp; This letterhead design is meant project an image<br>of professionalism reliability. By using simple aligen we have created a very spacious feeling.<br>The simplicity suggest&nbsp; rengththe spaciousnes contributes haesthetics the layout. These basic<br>qualities along with the (Your Company)</p>

  <p class="body-copy p2">look and helps reinforce the (Your Company) brand. letterhead design is meant to project an image<br>design. When positioned properly, it will serve to work in harmony all the other elements letterhead.<br>sionalism and reliability.</p>

  <p class="body-copy p3">This letterhead design is based on the (Form of your logo) form (Your Company) logo. Each stationery<br>we have created a very spacious feeling. The simplicity suggests strength the spaciousnes contribute<br>part of the (Form of your logo). This letterhead design is based on the (Form of your logo) form (Your<br>Company) logo. Each stationery we have created a very spacious feeling. The simplicity suggests<br>strength the spaciousnes contribute part of the (Form of your logo).</p>

  <div class="footer-rule"></div>
  <footer class="footer">
    <span class="address">4728 SW 81st Ter . Halverd Cove, Florida 39417</span>
    <span class="license">KRT8046392</span>
  </footer>
</main>
</body>
</html>
```